Business card

We need a business card design for our company based in Auckland , New Zealand called 'Ridge + Studio Ltd'. We provide architectural services. We would like to see designs that use the max. three colours (such as white, black, grey) The final design should communicate financial safety and growth."
Also I will provide our company logo. I would like to the logo to be embeded onto our business card.

Target Market(s)

new residential house, alteration & addition & light commericila design & drafting service

Industry/Entity Type

Architecture

Contact Information for Business Card

Company name: ridge + studio Ltd.
Name: Mark Delford
Job title: architectural designer & Design LBP
email address: mark@rplusd.co.nz
mobile number: 02 5163 2290
web site: www.rplusd.co.nz

Requirements
Must have
• My project must have..
• - embeded logo (attached company logo)
• I don't have a bigger version for our company logo, but I have one old one, so you can remove the word from it)
• - insert the attached small BKTW logo & LBP logo
• - creative, simple and clear business card.
• - Max. three colours
Nice to have
• - Here are the samples I would like to share with you: http://www.plimvora.com/blog/minimalistic-business-card-designs/
• I would like to have my business card like one of the creation.
Should not have
• TBA

```html
<!DOCTYPE html>
<html lang="en">
<head>
<meta charset="utf-8">
<title>Ridge + Studio Ltd — Business Card</title>
<link rel="stylesheet" href="https://fonts.googleapis.com/css2?family=PT+Sans:wght@400;700&family=Cinzel:wght@400&display=swap">
<style>
  :root {
    --backdrop: #141414;
    --card: #ffffff;
    --ink: #111111;
    --grey: #8a8a8a;
    --badge-dark: #2b2b2b;
  }
  * { margin: 0; padding: 0; box-sizing: border-box; }
  html, body {
    width: 1200px; height: 900px; overflow: hidden;
    background: var(--backdrop);
  }
  .stage { position: relative; width: 1200px; height: 900px; }
  .card {
    position: absolute; top: 307px;
    width: 439px; height: 270px;
    background: var(--card);
    border-radius: 12px;
    color: var(--ink);
  }
  .card--front { left: 149px; }
  .card--back { left: 609px; }

  /* Front */
  .brand-mark {
    position: absolute; left: 50px; top: 74px; width: 120px;
    display: flex; flex-direction: column; align-items: center;
  }
  .brand-mark__circle {
    width: 86px; height: 86px; border-radius: 50%;
    border: 6px solid var(--ink);
  }
  .brand-mark__name {
    margin-top: 12px;
    font: 400 12px/1 "Cinzel", serif;
    letter-spacing: 0.5px; white-space: nowrap;
  }
  .person { position: absolute; left: 202px; top: 74px; }
  .person__name { font: 700 15px/1.2 "PT Sans", sans-serif; }
  .person__role { font: 400 12px/1.3 "PT Sans", sans-serif; }
  .contacts {
    position: absolute; left: 202px; top: 146px;
    list-style: none;
    font: 400 12px/15.5px "PT Sans", sans-serif;
  }
  .contacts li { display: flex; align-items: center; gap: 7px; }
  .contacts svg { width: 9px; height: 9px; fill: var(--ink); flex: none; }

  /* Back */
  .company {
    position: absolute; left: 0; right: 0; top: 31px;
    display: flex; flex-direction: column; align-items: center;
  }
  .company__circle {
    width: 94px; height: 94px; border-radius: 50%;
    border: 6px solid var(--ink);
  }
  .company__name {
    margin-top: 15px;
    font: 400 17px/1 "Cinzel", serif;
    letter-spacing: 0.3px;
  }
  .memberships {
    position: absolute; left: 130px; top: 174px;
    display: flex; align-items: center; gap: 16px;
  }
  .membership--association {
    width: 86px; height: 64px; border-radius: 4px;
    background: var(--grey);
  }
  .membership--licence {
    width: 76px; height: 76px; border-radius: 50%;
    background: var(--badge-dark);
  }
</style>
</head>
<body>
<main class="stage">
  <section class="card card--front" aria-label="Business card front">
    <div class="brand-mark">
      <div class="brand-mark__circle"></div>
      <div class="brand-mark__name">ridge + studio</div>
    </div>
    <div class="person">
      <h1 class="person__name">Mark Delford</h1>
      <p class="person__role">Architectural designer &amp; Design LBP</p>
    </div>
    <ul class="contacts">
      <li>
        <svg viewBox="0 0 10 10" aria-hidden="true"><path d="M2 0.5 L3.6 0.5 L4.3 2.8 L3.2 3.7 Q4 5.8 6.3 6.8 L7.2 5.7 L9.5 6.4 L9.5 8 Q9 9.6 7.4 9.5 Q1.5 8.6 0.5 2.6 Q0.5 0.9 2 0.5 Z"/></svg>
        02 5163 2290
      </li>
      <li>
        <svg viewBox="0 0 10 10" aria-hidden="true"><path d="M0.5 2 H9.5 V8.5 H0.5 Z M1.3 2.8 L5 5.6 L8.7 2.8 Z" fill-rule="evenodd"/></svg>
        mark@rplusd.co.nz
      </li>
      <li>
        <svg viewBox="0 0 10 10" aria-hidden="true"><circle cx="5" cy="5" r="4.5"/></svg>
        www.rplusd.co.nz
      </li>
    </ul>
  </section>

  <section class="card card--back" aria-label="Business card back">
    <div class="company">
      <div class="company__circle"></div>
      <h2 class="company__name">RIDGE + STUDIO LTD.</h2>
    </div>
    <div class="memberships">
      <div class="membership--association" role="img" aria-label="BKTW professional member badge"></div>
      <div class="membership--licence" role="img" aria-label="Licensed building practitioner badge"></div>
    </div>
  </section>
</main>
</body>
</html>
```